Los Angeles based Demolition, Grading, and Structural concrete Contractor in need of a Sale brochure

We are a Los Angeles-based demolition, grading, and structural concrete contractor looking for a professionally designed sales brochure that represents our company and services. The brochure should be visually appealing, easy to read, and include the following:

-Company Logo: Prominently displayed to enhance brand identity.

-Services We Offer: A clear breakdown of our key services, including demolition, grading, and structural concrete work.

-Project Scope & Capabilities: A brief explanation of the type of projects we handle (residential, commercial, industrial).

-Pricing Information: Mention that demolition services start at $20,000. This price includes complete demolition of structure, safe debris removal and hauling, site preparation for new construction.

-Contact Information: Our phone number(818.502.6617), email(contact@brovanbuildersinc.example) , and website for potential clients to reach out.

The design should reflect the professionalism and strength of our industry, using a modern, clean layout with bold colors that align with construction and demolition themes. Images of past work or stock photos representing our services are encouraged.

Final deliverables should be print-ready (PDF) and digital-friendly formats. Looking forward to creative and impactful designs!

```html
<!DOCTYPE html>
<html lang="en">
<head>
<meta charset="UTF-8">
<title>Brovan Builders – Company Brochure 2025</title>
<link href="https://fonts.googleapis.com/css2?family=Poppins:wght@300;400;700;800&display=swap" rel="stylesheet">
<style>
  :root {
    --brand-blue: #1a75bd;
    --year-blue: #a7c6e9;
    --white: #ffffff;
  }
  * { margin: 0; padding: 0; box-sizing: border-box; }
  html, body { width: 1200px; height: 849px; overflow: hidden; background: var(--white); }
  body { font-family: 'Poppins', sans-serif; position: relative; }

  .site-photo { position: absolute; }
  .site-photo--retaining {
    left: 0; top: 0; width: 600px; height: 627px;
    background: linear-gradient(180deg,
      #7f8183 0%, #8f9193 14%, #a2a4a6 24%,
      #5e6062 32%, #707274 40%, #8a8c8e 47%,
      #b4b5b6 58%, #c3c4c5 70%, #b9babb 80%,
      #5f6163 88%, #9a9b9c 96%, #b0b1b2 100%);
  }
  .site-photo--excavation {
    left: 636px; top: 144px; width: 529px; height: 483px;
    background: linear-gradient(180deg,
      #6f94bd 0%, #c6d6e6 10%, #eef2f6 18%, #b8c8d8 26%,
      #d9e1e8 34%, #a7b0ad 40%, #7e8a6f 45%, #5e6b4c 49%,
      #b79566 54%, #d1aa72 64%, #c89a5f 76%,
      #b88648 86%, #a9773e 94%, #c49860 100%);
  }

  .brand {
    position: absolute; left: 636px; top: 44px;
    display: flex; align-items: center; gap: 10px;
  }
  .brand__mark { width: 20px; height: 20px; background: var(--brand-blue); }
  .brand__name {
    font-weight: 800; font-size: 32px; letter-spacing: 1px;
    color: var(--brand-blue); line-height: 1;
  }

  .footer-band {
    position: absolute; left: 0; top: 627px; width: 1200px; height: 222px;
    background: var(--brand-blue); color: var(--white);
  }
  .contact__title {
    position: absolute; left: 44px; top: 29px;
    font-weight: 700; font-size: 27px; line-height: 1;
  }
  .contact__list { list-style: none; position: absolute; left: 44px; top: 93px; }
  .contact__item {
    display: flex; align-items: center; gap: 16px;
    height: 25px; margin-bottom: 11px;
    font-weight: 400; font-size: 22.5px; line-height: 1;
  }
  .contact__icon { width: 25px; height: 25px; flex: none; }

  .cover-title {
    position: absolute; left: 634px; top: 53px;
    font-weight: 700; font-size: 59px; line-height: 63px; letter-spacing: 0.5px;
  }
  .cover-year {
    position: absolute; left: 1104px; top: 20px;
    writing-mode: vertical-rl;
    font-weight: 300; font-size: 70px; line-height: 1; letter-spacing: 3px;
    color: var(--year-blue);
  }
</style>
</head>
<body>
  <div class="site-photo site-photo--retaining" role="img" aria-label="Black and white photo of a hillside site with terraced concrete retaining walls and a tracked loader"></div>

  <div class="brand">
    <span class="brand__mark"></span>
    <span class="brand__name">BROVAN BUILDERS</span>
  </div>

  <div class="site-photo site-photo--excavation" role="img" aria-label="Colour photo of a hillside excavation with an orange mini excavator, rebar bundles and a city view below a cloudy sky"></div>

  <footer class="footer-band">
    <h2 class="contact__title">CONTACT US</h2>
    <ul class="contact__list">
      <li class="contact__item">
        <svg class="contact__icon" viewBox="0 0 24 24"><circle cx="12" cy="12" r="12" fill="#fff"/><path d="M8.2 6.5l1.9-.4 1.2 3-1.3 1c.6 1.4 1.6 2.5 3 3.2l1-1.3 3 1.1-.3 2c-.1.5-.6.8-1.1.8-4.6-.4-8.4-4.1-8.8-8.7 0-.4.3-.7.7-.8z" fill="#1a75bd"/></svg>
        <span>818.502.6617</span>
      </li>
      <li class="contact__item">
        <svg class="contact__icon" viewBox="0 0 24 24"><circle cx="12" cy="12" r="12" fill="#fff"/><g fill="none" stroke="#1a75bd" stroke-width="1.3"><circle cx="12" cy="12" r="6.5"/><ellipse cx="12" cy="12" rx="2.8" ry="6.5"/><path d="M5.5 12h13M6.5 8.8h11M6.5 15.2h11"/></g></svg>
        <span>CONTACT US</span>
      </li>
      <li class="contact__item">
        <svg class="contact__icon" viewBox="0 0 24 24"><circle cx="12" cy="12" r="12" fill="#fff"/><g fill="none" stroke="#1a75bd" stroke-width="1.4"><rect x="6" y="8" width="12" height="8.5" rx="1"/><path d="M6.3 8.5l5.7 4.6 5.7-4.6M6.3 16l4.2-3.6M17.7 16l-4.2-3.6"/></g></svg>
        <span>contact@brovanbuildersinc.example</span>
      </li>
    </ul>

    <h1 class="cover-title">COMPANY<br>BROCHURE</h1>
    <div class="cover-year">2025</div>
  </footer>
</body>
</html>
```